Business cards to launch an education platform

Hi,
I am looking at having new business cards designed.
I am a startup, developing a web platform for schools and university, the education world. It's an online assessment system.
I would like a card that looks classy, and that is using the colors and the font of my logo.

I have attached:
1) my logo
2) A business card that I have designed quickly so you can have all the information required in the card, but I really don't like it.
3) The font that I am using (Lato Regular) to design my web platform
4) Some screenshots of my web platform so you can have a look at the style that I have.

Target Market(s)

Major market: Education system: Schools and university
Minor markets: Business in general

Industry/Entity Type

Business

Contact Information for Business Card

Clara Fenwick
Director

M: 0437 518 902
E: clara.fenwick@amberLoomSystems.com.au

Requirements
Must have
• The colors of my logo

```html
<!DOCTYPE html>
<html lang="en">
<head>
<meta charset="utf-8">
<title>Amber Loom Systems — Business Card</title>
<link href="https://fonts.googleapis.com/css2?family=Lato:wght@400;700&display=swap" rel="stylesheet">
<style>
  :root {
    --backdrop: #e9ebee;
    --paper: #ffffff;
    --navy: #0d4f8f;
    --blue-top: #0b72c9;
    --blue-bottom: #05427f;
    --cyan: #12d4ee;
    --white: #ffffff;
  }
  * { margin: 0; padding: 0; box-sizing: border-box; }
  html, body {
    width: 1200px; height: 900px; overflow: hidden;
    background: var(--backdrop);
    font-family: "Lato", sans-serif;
  }
  .canvas { position: relative; width: 1200px; height: 900px; }

  .card { position: absolute; overflow: hidden; box-shadow: 0 6px 18px rgba(0,0,0,.18); }

  /* Front */
  .card--front { left: 78px; top: 34px; width: 588px; height: 363px; background: var(--paper); }
  .card__bands { position: absolute; inset: 0; }
  .brand { position: absolute; left: 127px; top: 66px; display: flex; align-items: center; gap: 22px; }
  .brand__square { width: 86px; height: 86px; background: var(--navy); }
  .brand__name {
    color: var(--navy); font-weight: 400; font-size: 37px; line-height: 1.05;
    letter-spacing: 2px;
  }
  .contact {
    position: absolute; right: 200px; top: 262px;
    color: var(--white); font-size: 16px; text-align: right;
  }
  .contact__row { display: flex; align-items: center; justify-content: flex-end; gap: 9px; height: 26px; }
  .contact__icon { width: 13px; height: 13px; fill: var(--white); }
  .person { position: absolute; left: 421px; top: 259px; color: var(--white); }
  .person__name { font-size: 23px; font-weight: 400; }
  .person__role { font-size: 16px; margin-top: 4px; }

  /* Back */
  .card--back {
    left: 388px; top: 505px; width: 567px; height: 352px;
    background: linear-gradient(180deg, var(--blue-top), var(--blue-bottom));
  }
  .back-brand {
    position: absolute; right: 30px; bottom: 48px; text-align: right;
    color: var(--white); font-weight: 400; font-size: 38px; line-height: 1.1; letter-spacing: 3px;
  }
</style>
</head>
<body>
<main class="canvas">

  <section class="card card--front" aria-label="Business card front">
    <svg class="card__bands" width="588" height="363" viewBox="0 0 588 363" aria-hidden="true">
      <defs>
        <linearGradient id="front-blue" x1="0" y1="0" x2="0" y2="1">
          <stop offset="0" stop-color="#0b72c9"/>
          <stop offset="1" stop-color="#05427f"/>
        </linearGradient>
      </defs>
      <polygon points="0,199 404,199 383,225 0,225" fill="#12d4ee"/>
      <polygon points="0,229 385,229 414,192 588,192 588,363 0,363" fill="url(#front-blue)"/>
    </svg>

    <div class="brand">
      <div class="brand__square"></div>
      <div class="brand__name">AMBER LOOM<br>Systems</div>
    </div>

    <div class="contact">
      <div class="contact__row">
        <span>0437 518 902</span>
        <svg class="contact__icon" viewBox="0 0 24 24" aria-hidden="true"><path d="M6.6 10.8a15.2 15.2 0 0 0 6.6 6.6l2.2-2.2a1 1 0 0 1 1-.25 11.4 11.4 0 0 0 3.6.57 1 1 0 0 1 1 1V20a1 1 0 0 1-1 1A17 17 0 0 1 3 4a1 1 0 0 1 1-1h3.5a1 1 0 0 1 1 1c0 1.25.2 2.45.57 3.57a1 1 0 0 1-.25 1z"/></svg>
      </div>
      <div class="contact__row">
        <span>clara.fenwick@amberLoomSystems.com.au</span>
        <svg class="contact__icon" viewBox="0 0 24 24" aria-hidden="true"><path d="M2 5h20v14H2z M3.5 6.5 12 13l8.5-6.5" fill="#ffffff" stroke="#0a5aa6" stroke-width="1.6"/></svg>
      </div>
    </div>

    <div class="person">
      <div class="person__name">Clara Fenwick</div>
      <div class="person__role">Director</div>
    </div>
  </section>

  <section class="card card--back" aria-label="Business card back">
    <div class="back-brand">AMBER LOOM<br>Systems</div>
  </section>

</main>
</body>
</html>
```